A start-up named "Corvane Therapeutics" - needs a new PowerPoint design

We need a new PowerPoint Design for an early-stage start-up named "Corvane Therapeutics" seeking to disrupt the current approach towards drug discovery within aging disorders.

We would like to build on Corvane's legacy, the founder of the modern science of genetics, by employing a multidisciplinary approach, experimenting, and providing elderly patients the attention they deserve.

We have selected the suffix "therapeutics" intentionally as it stands for (a medicine) the treatment of disease; the science of healing. Alzheimer’s treatment is a huge, urgent, unmet need:
- Shift from a disease-management system to a preventive medicine system
- Focus on increasing the health span, not only the life span

Target Market(s)

Pharma/ Biotech Executives Medical Institutions Healthcare professionals (MDs, nurses, payors, pharmacists, etc.) Patients

Industry/Entity Type

Healthcare

Other font styles liked:
• Celias

Colors
0054AA
0677BA
7BADD7
CADEEF
E8F1F8
E54698
E96AAD
F1A4CE
F9D9EA
FCEFF6
A7469A
B969AE
D3A5CF
EDDBEB
F8F0F9
6B429C
8869AF
B7A5CE
E3DAEB
F3F0F8

Requirements
Must have
• - differentiate from other companies named after Corvane - differentiate from other Pharma/ Biotech companies
Nice to have
• simplicity/ minimalist logo vivid colors gradient 3D Life-Sciences inspired Simple geometry Balance
Should not have
• mascot/ emblem watermark logo animated ink style nature-inspired inventive typography artistic chaos

```html
<!DOCTYPE html>
<html lang="en">
<head>
<meta charset="utf-8">
<title>Corvane Therapeutics – Presentation Slides</title>
<link href="https://fonts.googleapis.com/css2?family=Poppins:wght@500;600;700&family=Roboto:wght@400;500&display=swap" rel="stylesheet">
<style>
:root{
  --canvas:#7a7a7a;
  --plum:#7f0b57;
  --plum-mid:#95146b;
  --plum-deep:#6a0848;
  --magenta:#a0166f;
  --blue:#1e64b8;
  --orange:#e5a020;
  --white:#ffffff;
  --paper:#e9e9e9;
  --ink:#2b2b2b;
  --sky:#4aa3d8;
  --sky-deep:#0d5f96;
}
*{box-sizing:border-box;margin:0;padding:0}
html,body{width:1200px;height:1069px;overflow:hidden;background:var(--canvas)}
body{position:relative;font-family:"Roboto",sans-serif}
.slide-frame{position:absolute;width:510.5px;height:287.2px;overflow:hidden}
.slide{position:absolute;left:0;top:0;width:869px;height:489px;transform:scale(.5874);transform-origin:0 0;overflow:hidden;background:linear-gradient(135deg,var(--plum-mid),var(--plum) 60%,var(--plum-deep))}
.slide > *{position:absolute}
.decor{left:0;top:0;width:869px;height:489px}
.brand{display:flex;align-items:center;gap:8px;font-family:"Poppins",sans-serif;font-weight:500;font-size:19px;color:var(--white);line-height:1}
.brand-mark{width:12px;height:12px;background:var(--white)}
.brand.dark{color:var(--plum)}
.brand.dark .brand-mark{background:var(--plum)}
.heading{font-family:"Poppins",sans-serif;font-weight:700;color:var(--white);font-size:24px;line-height:1.35;text-transform:uppercase}
.body-copy{font-size:8px;line-height:15.3px;color:var(--white);text-align:justify}
.body-copy.dark{color:var(--ink)}
.accent{color:var(--orange)}
.plum-text{color:var(--plum)}

/* slide 1 */
.slide-welcome{background:linear-gradient(120deg,#8c0c5c 0%,#9b1470 40%,#6a2a92 70%,#0a6cbd 100%)}
.brand-word-large{left:470px;top:190px;font-family:"Poppins",sans-serif;font-weight:600;font-size:64px;color:#4fa6e4}
.social-row{left:50px;top:440px;display:flex;gap:6px}
.social-dot{width:19px;height:19px;border:1.5px solid var(--white);border-radius:50%}

/* slide 3 */
.slide-about{background:var(--white)}
.feature{display:flex;gap:18px;align-items:flex-start;width:300px}
.feature-badge{width:64px;height:58px;flex:none}
.feature-title{font-family:"Poppins",sans-serif;font-weight:600;font-size:12px;color:var(--white);margin-bottom:4px}
.feature-copy{font-size:8px;line-height:13px;color:var(--white);text-align:justify;width:164px}

/* slide 4 */
.axis-label{font-size:7px;color:var(--orange);font-family:"Poppins",sans-serif}
.chart-caption{font-family:"Poppins",sans-serif;font-weight:600;font-size:10px;color:var(--white)}
.point-list{left:546px;top:158px;width:230px;list-style:none}
.point-list li{position:relative;padding-left:20px;font-size:7px;line-height:13px;color:var(--white);margin-bottom:36px}
.point-list li::before{content:"";position:absolute;left:0;top:13px;width:7px;height:7px;border-radius:50%;background:var(--orange)}

/* slide 5 */
.stat{width:200px}
.stat-figure{font-family:"Poppins",sans-serif;font-weight:700;font-size:30px;color:var(--plum);line-height:1}
.stat-label{font-family:"Poppins",sans-serif;font-weight:700;font-size:14px;color:var(--orange);margin:6px 0 4px}
.stat-copy{font-size:7.5px;line-height:15px;color:var(--ink)}
.sub-heading{font-family:"Poppins",sans-serif;font-weight:700;font-size:17px;color:var(--white)}

/* slide 6 */
.contact-list{list-style:none;left:52px;top:266px}
.contact-list li{display:flex;align-items:center;gap:8px;font-size:9.5px;color:var(--white);height:33px}
.contact-icon{width:14px;height:14px;border-radius:50%;background:var(--orange);flex:none;display:flex;align-items:center;justify-content:center}
</style>
</head>
<body>

<!-- Welcome -->
<div class="slide-frame" style="left:75.2px;top:77px">
  <section class="slide slide-welcome">
    <div class="brand" style="left:50px;top:26px"><span class="brand-mark"></span>Corvane</div>
    <h1 class="heading" style="left:51px;top:148px">Welcome to Corvane<br>Therapeutics</h1>
    <p class="body-copy" style="left:51px;top:225px;width:298px">Lorem ipsum dolor sit amet, consectetur adipiscing elit, sed do eiusmod tempor incididunt ut labore et dolore magna aliqua. Ut enim ad minim veniam, quis nostrud exercitation ullamco laboris nisi ut aliquip ex ea commodo consequat. Duis aute irure dolor in reprehenderit in voluptate velit esse cillum dolore eu fugiat nulla pariatur. Excepteur sint occaecat cupidatat non proident, sunt in culpa qui officia deserunt mollit anim id est laborum.</p>
    <div class="brand-word-large">Corvane</div>
    <div class="social-row"><span class="social-dot"></span><span class="social-dot"></span><span class="social-dot"></span><span class="social-dot"></span></div>
  </section>
</div>

<!-- Intro with molecule image -->
<div class="slide-frame" style="left:606.2px;top:77px">
  <section class="slide">
    <svg class="decor" viewBox="0 0 869 489">
      <polygon points="605,0 869,0 869,448 442,448" fill="var(--orange)"/>
      <polygon points="650,0 869,0 869,420 490,420" fill="var(--paper)"/>
      <polygon points="684,0 869,0 869,390 535,390" fill="url(#mol)" role="img" aria-label="Photograph of blue glass molecule models"/>
      <polygon points="550,140 600,15 630,22 580,148" fill="var(--plum)" stroke="var(--white)" stroke-width="1.5"/>
      <polyline points="395,489 462,300 493,306 446,489" fill="none" stroke="var(--white)" stroke-width="1.5"/>
      <defs><linearGradient id="mol" x1="0" y1="0" x2="1" y2="1"><stop offset="0" stop-color="#bfe2f6"/><stop offset=".5" stop-color="var(--sky)"/><stop offset="1" stop-color="var(--sky-deep)"/></linearGradient></defs>
    </svg>
    <div class="brand" style="left:51px;top:26px"><span class="brand-mark"></span>Corvane</div>
    <h2 class="heading" style="left:51px;top:140px">Lorem ipsum dolor<br>sit amet,</h2>
    <p class="body-copy" style="left:51px;top:216px;width:312px">Lorem ipsum dolor sit amet, consectetur adipiscing elit, sed do eiusmod tempor incididunt ut labore et dolore magna aliqua. Ut enim ad minim veniam, quis nostrud exercitation ullamco laboris nisi ut aliquip ex ea commodo consequat. Duis aute irure dolor in reprehenderit in voluptate velit esse cillum dolore eu fugiat nulla pariatur. Excepteur sint occaecat cupidatat non proident, sunt in culpa qui officia deserunt mollit anim id est laborum ex ea commodo consequat. Duis aute irure dolor in reprehenderit in voluptate velit esse cillum dolore eu fugiat nulla pariatur. Excepteur sint occaecat cupidatat non proident,in</p>
  </section>
</div>

<!-- About company -->
<div class="slide-frame" style="left:75.2px;top:384px">
  <section class="slide slide-about">
    <svg class="decor" viewBox="0 0 869 489">
      <defs><linearGradient id="aboutBg" x1="0" y1="0" x2="1" y2="1"><stop offset="0" stop-color="var(--plum-mid)"/><stop offset="1" stop-color="var(--plum-deep)"/></linearGradient></defs>
      <polygon points="492,0 869,0 869,489 367,489" fill="url(#aboutBg)"/>
      <polygon points="446,0 492,0 394,433 358,428" fill="var(--orange)"/>
      <polyline points="444,0 340,432 370,438" fill="none" stroke="var(--plum)" stroke-width="1.2"/>
      <polygon points="786,442 804,446 788,489 770,489" fill="var(--orange)"/>
      <polyline points="800,432 815,436 797,489" fill="none" stroke="var(--white)" stroke-width="2"/>
      <g>
        <polygon points="545,60 609,60 595,88 609,116 545,116 559,88" fill="var(--orange)"/><polygon points="590,88 609,60 609,116" fill="var(--white)"/>
        <polygon points="519,155 583,155 569,183 583,211 519,211 533,183" fill="var(--orange)"/><polygon points="564,183 583,155 583,211" fill="var(--white)"/>
        <polygon points="493,255 557,255 543,283 557,311 493,311 507,283" fill="var(--orange)"/><polygon points="538,283 557,255 557,311" fill="var(--white)"/>
        <polygon points="467,360 531,360 517,388 531,416 467,416 481,388" fill="var(--orange)"/><polygon points="512,388 531,360 531,416" fill="var(--white)"/>
      </g>
      <g fill="none" stroke="var(--white)" stroke-width="1.6">
        <circle cx="576" cy="86" r="9"/><circle cx="551" cy="183" r="9"/><circle cx="524" cy="281" r="9"/><circle cx="498" cy="387" r="9"/>
      </g>
    </svg>
    <div class="brand dark" style="left:51px;top:26px"><span class="brand-mark"></span>Corvane</div>
    <h2 class="heading plum-text" style="left:50px;top:153px;font-size:31px;line-height:1.22">About<br><span class="accent">Company</span></h2>
    <p class="body-copy dark" style="left:51px;top:240px;width:270px">Lorem ipsum dolor sit amet, consectetur adipiscing elit, sed do eiusmod tempor incididunt ut labore et dolore magna aliqua. Ut enim ad minim veniam, quis nostrud exercitation ullamco laboris nisi ut aliquip ex ea commodo consequat. Duis aute irure dolor in reprehenderit in voluptate velit esse cillum dolore eu fugiat nulla pariatur. Excepteur sint occaecat cupidatat non proident, sunt in culpa qui officia deserunt mollit anim id est laborum</p>
    <div style="left:629px;top:57px"><h3 class="feature-title">Lorem Ipsum</h3><p class="feature-copy">Lorem ipsum dolor sit amet, consectetur adipiscing elit, sed do eiusmod tempor incididunt ut labore et</p></div>
    <div style="left:603px;top:152px"><h3 class="feature-title">Lorem Ipsum</h3><p class="feature-copy">Lorem ipsum dolor sit amet, consectetur adipiscing elit, sed do eiusmod tempor incididunt ut labore et</p></div>
    <div style="left:577px;top:252px"><h3 class="feature-title">Lorem Ipsum</h3><p class="feature-copy">Lorem ipsum dolor sit amet, consectetur adipiscing elit, sed do eiusmod tempor incididunt ut labore et</p></div>
    <div style="left:551px;top:356px"><h3 class="feature-title">Lorem Ipsum</h3><p class="feature-copy">Lorem ipsum dolor sit amet, consectetur adipiscing elit, sed do eiusmod tempor incididunt ut labore et</p></div>
  </section>
</div>

<!-- Growth chart -->
<div class="slide-frame" style="left:606.2px;top:384px">
  <section class="slide">
    <svg class="decor" viewBox="0 0 869 489">
      <g stroke="var(--orange)" stroke-width="2" fill="none"><polyline points="115,135 115,424 400,424"/></g>
      <g fill="var(--white)">
        <rect x="138" y="377" width="11" height="45"/><rect x="165" y="352" width="11" height="70"/><rect x="192" y="320" width="11" height="102"/><rect x="219" y="290" width="11" height="132"/><rect x="246" y="258" width="11" height="164"/><rect x="273" y="228" width="11" height="194"/><rect x="300" y="203" width="11" height="219"/><rect x="327" y="181" width="11" height="241"/><rect x="354" y="160" width="11" height="262"/><rect x="381" y="137" width="11" height="285"/>
      </g>
      <polyline points="143,371 152,346 170,340 197,311 224,279 251,249 278,219 305,193 332,173 359,150 386,128 402,126" fill="none" stroke="var(--orange)" stroke-width="1.2"/>
      <g fill="var(--orange)">
        <circle cx="143" cy="371" r="3"/><circle cx="170" cy="340" r="3"/><circle cx="197" cy="311" r="3"/><circle cx="224" cy="279" r="3"/><circle cx="251" cy="249" r="3"/><circle cx="278" cy="219" r="3"/><circle cx="305" cy="193" r="3"/><circle cx="332" cy="173" r="3"/><circle cx="359" cy="150" r="3"/><circle cx="386" cy="128" r="3"/>
      </g>
      <g class="axis-label" fill="var(--orange)" font-size="7" text-anchor="end" font-family="Poppins, sans-serif">
        <text x="107" y="152">90</text><text x="107" y="175">80</text><text x="107" y="194">70</text><text x="107" y="221">60</text><text x="107" y="250">50</text><text x="107" y="282">40</text><text x="107" y="314">30</text><text x="107" y="343">20</text><text x="107" y="373">10</text>
      </g>
      <g fill="var(--orange)" font-size="7" text-anchor="middle" font-family="Poppins, sans-serif">
        <text x="144" y="436">2012</text><text x="171" y="436">2013</text><text x="198" y="436">2014</text><text x="225" y="436">2015</text><text x="252" y="436">2016</text><text x="279" y="436">2017</text><text x="306" y="436">2018</text><text x="333" y="436">2019</text><text x="360" y="436">2021</text><text x="387" y="436">2022</text>
      </g>
    </svg>
    <div class="brand" style="left:51px;top:26px"><span class="brand-mark"></span>Corvane</div>
    <div class="chart-caption" style="left:112px;top:106px">Lorem ipsum</div>
    <div class="chart-caption" style="left:442px;top:415px">Lorem ipsum</div>
    <h2 class="heading" style="left:546px;top:74px;text-transform:none;font-size:22px">Lorem ipsum</h2>
    <ul class="point-list">
      <li>Lorem ipsum dolor sit amet, consectetur adipiscing elit, sed do eiusmod tempor incididunt ut labore et dolore magna aliqua. Ut enim ad minim veniam, quis nostrud exercitation</li>
      <li>Lorem ipsum dolor sit amet, consectetur adipiscing elit, sed do eiusmod tempor incididunt ut labore et dolore magna aliqua. Ut enim ad minim veniam, quis nostrud exercitation</li>
      <li>Lorem ipsum dolor sit amet, consectetur adipiscing elit, sed do eiusmod tempor incididunt ut labore et dolore magna aliqua. Ut enim ad minim veniam, quis nostrud exercitation</li>
      <li>Lorem ipsum dolor sit amet, consectetur adipiscing elit, sed do eiusmod tempor incididunt ut labore et dolore magna aliqua. Ut enim ad minim veniam, quis nostrud exercitation</li>
    </ul>
  </section>
</div>

<!-- Mission and vision -->
<div class="slide-frame" style="left:75.2px;top:691px">
  <section class="slide">
    <svg class="decor" viewBox="0 0 869 489">
      <polygon points="440,0 869,0 869,489 533,489" fill="var(--white)"/>
      <polygon points="409,0 440,0 536,404 505,408" fill="var(--orange)"/>
      <polyline points="389,0 488,422 518,418" fill="none" stroke="var(--white)" stroke-width="1.5"/>
      <polygon points="840,0 869,0 869,56 826,50" fill="var(--orange)"/>
      <polyline points="830,0 806,60 842,68 850,50" fill="none" stroke="var(--plum)" stroke-width="1.5"/>
    </svg>
    <h2 class="heading" style="left:50px;top:38px;line-height:1.5">Our Mission<br><span class="accent">and our vision</span></h2>
    <h3 class="sub-heading" style="left:51px;top:136px">OUR MISSION</h3>
    <p class="body-copy" style="left:51px;top:166px;width:308px">Lorem ipsum dolor sit amet, consectetur adipiscing elit, sed do eiusmod tempor incididunt ut labore et dolore magna aliqua. Ut enim ad minim veniam, quis nostrud exercitation ullamco laboris nisi ut aliquip ex ea commodo consequat.Duis aute irure dolor in reprehenderit in voluptate velit esse cillum dolore eu fugiat nulla pariatur. Excepteur sint occaecat cupidatat non proident,</p>
    <h3 class="sub-heading accent" style="left:51px;top:272px">OUR MISSION</h3>
    <p class="body-copy" style="left:51px;top:302px;width:308px">Lorem ipsum dolor sit amet, consectetur adipiscing elit, sed do eiusmod tempor incididunt ut labore et dolore magna aliqua. Ut enim ad minim veniam, quis nostrud exercitation ullamco laboris nisi ut aliquip ex ea commodo consequat.Duis aute irure dolor in reprehenderit in voluptate velit esse cillum dolore eu fugiat nulla pariatur. Excepteur sint occaecat cupidatat non proident,</p>
    <div class="stat" style="left:550px;top:58px"><div class="stat-figure">72 %</div><div class="stat-label">LOREM IPSUM</div><p class="stat-copy">Lorem ipsum dolor sit amet, consectetur adipiscing elit, sed do eiusmod tempor incididunt ut labore et dolore</p></div>
    <div class="stat" style="left:577px;top:181px"><div class="stat-figure">25%</div><div class="stat-label">LOREM IPSUM</div><p class="stat-copy">Lorem ipsum dolor sit amet, consectetur adipiscing elit, sed do eiusmod tempor incididunt ut labore et dolore</p></div>
    <div class="stat" style="left:609px;top:307px"><div class="stat-figure">3%</div><div class="stat-label">LOREM IPSUM</div><p class="stat-copy">Lorem ipsum dolor sit amet, consectetur adipiscing elit, sed do eiusmod tempor incididunt ut labore et dolore</p></div>
    <div class="brand dark" style="left:720px;top:432px"><span class="brand-mark"></span>Corvane</div>
  </section>
</div>

<!-- Contact -->
<div class="slide-frame" style="left:606.2px;top:691px">
  <section class="slide">
    <svg class="decor" viewBox="0 0 869 489">
      <polygon points="605,0 869,0 869,448 442,448" fill="var(--orange)"/>
      <polygon points="650,0 869,0 869,420 490,420" fill="var(--paper)"/>
      <polygon points="684,0 869,0 869,390 535,390" fill="url(#bact)" role="img" aria-label="Microscope image of blue rod-shaped bacteria"/>
      <polygon points="550,140 600,15 630,22 580,148" fill="var(--plum)" stroke="var(--white)" stroke-width="1.5"/>
      <polyline points="395,489 462,300 493,306 446,489" fill="none" stroke="var(--white)" stroke-width="1.5"/>
      <defs><linearGradient id="bact" x1="0" y1="0" x2="1" y2="1"><stop offset="0" stop-color="#0a4f78"/><stop offset=".5" stop-color="#2a9fcf"/><stop offset="1" stop-color="#063a5c"/></linearGradient></defs>
    </svg>
    <div class="brand" style="left:51px;top:26px"><span class="brand-mark"></span>Corvane</div>
    <h2 class="heading" style="left:51px;top:152px">Get in touch</h2>
    <p class="body-copy" style="left:51px;top:192px;width:318px">ex ea commodo consequat. Duis aute irure dolor in reprehenderit in voluptate velit esse cillum dolore eu fugiat nulla pariatur. Excepteur sint occaecat cupidatat non proident, sunt in culpa qui officia deserunt mollit anim id est laborum</p>
    <ul class="contact-list">
      <li><span class="contact-icon"><svg width="8" height="9" viewBox="0 0 8 9"><path d="M4 9C1 5.5 1 4.6 1 3.6a3 3 0 0 1 6 0C7 4.6 7 5.5 4 9z" fill="#fff"/><circle cx="4" cy="3.6" r="1.1" fill="#e5a020"/></svg></span>50,Lorem ipsum dolor sit</li>
      <li><span class="contact-icon"><svg width="8" height="6" viewBox="0 0 8 6"><rect x=".5" y=".5" width="7" height="5" fill="none" stroke="#fff"/><path d="M.5 .5L4 3.3 7.5 .5" fill="none" stroke="#fff"/></svg></span>info@corvanetherapeutics.com</li>
      <li><span class="contact-icon"><svg width="8" height="8" viewBox="0 0 8 8"><path d="M1.5 .5l1.6 1.8-.8 1.1c.6 1 1.3 1.7 2.3 2.3l1.1-.8 1.8 1.6-1 1C3.5 7.5.5 4.5.5 1.5z" fill="#fff"/></svg></span>+1 555 0142 000</li>
      <li><span class="contact-icon"><svg width="9" height="9" viewBox="0 0 9 9" fill="none" stroke="#fff" stroke-width=".8"><circle cx="4.5" cy="4.5" r="3.8"/><ellipse cx="4.5" cy="4.5" rx="1.6" ry="3.8"/><path d="M.7 4.5h7.6"/></svg></span>www.CorvaneTherapeutics.com</li>
    </ul>
  </section>
</div>

</body>
</html>
```